wealth management firm, professional group, new model

we have a logo that works but we need a card, white background using our colors...clean look

our tag line if can be used in

The Path From Saver to Steward

```html
<!DOCTYPE html>
<html lang="en">
<head>
<meta charset="utf-8">
<title>Arcvale Wealth Partners – Business Card</title>
<link href="https://fonts.googleapis.com/css2?family=Montserrat:wght@400;500;700&display=swap" rel="stylesheet">
<style>
  :root {
    --navy: #1b3360;
    --white: #ffffff;
    --ink: #2a2f3a;
    --stage: #2c2c2e;
  }
  * { box-sizing: border-box; margin: 0; padding: 0; }
  html, body { width: 1200px; height: 900px; overflow: hidden; }
  body {
    background: var(--stage);
    font-family: "Montserrat", sans-serif;
    position: relative;
  }
  .card {
    position: absolute;
    border-radius: 26px;
    overflow: hidden;
  }

  /* Front: portrait navy card, brand reading top to bottom */
  .card-front {
    left: 90px; top: 150px;
    width: 343px; height: 600px;
    background: var(--navy);
  }
  .front-brand {
    position: absolute;
    left: 290px; top: 60px;
    transform-origin: left top;
    transform: rotate(90deg);
    color: var(--white);
    white-space: nowrap;
  }
  .front-brand .brand-main { display: block; font-weight: 400; font-size: 62px; letter-spacing: 22px; line-height: 1; }
  .front-brand .brand-sub { display: block; font-weight: 400; font-size: 23px; letter-spacing: 6px; margin-top: 14px; }

  /* Back: white card with navy side band */
  .card-back {
    left: 500px; top: 278px;
    width: 610px; height: 348px;
    background: var(--white);
  }
  .back-band {
    position: absolute; left: 0; top: 0; bottom: 0;
    width: 172px;
    background: var(--navy);
  }
  .back-brand {
    position: absolute;
    left: 52px; top: 322px;
    transform-origin: left top;
    transform: rotate(-90deg);
    color: var(--white);
    white-space: nowrap;
  }
  .back-brand .brand-main { display: block; font-weight: 400; font-size: 40px; letter-spacing: 14px; line-height: 1; }
  .back-brand .brand-sub { display: block; font-weight: 400; font-size: 15px; letter-spacing: 4px; margin-top: 10px; }

  .contact {
    position: absolute;
    right: 34px; top: 36px;
    width: 380px;
    text-align: right;
    color: var(--ink);
  }
  .contact-name { color: var(--navy); font-weight: 700; font-size: 27px; line-height: 1.2; }
  .contact-title { font-size: 14px; margin-top: 4px; }
  .rule-short { width: 84px; height: 2px; background: var(--navy); margin: 14px 0 14px auto; }
  .contact-address { font-size: 14px; line-height: 1.45; }
  .contact-lines { list-style: none; margin-top: 14px; font-size: 14px; line-height: 1.65; }
  .contact-lines li { display: flex; justify-content: flex-end; align-items: center; gap: 8px; }
  .contact-lines svg { width: 12px; height: 12px; fill: var(--navy); flex: none; }
  .rule-long { height: 1.5px; background: var(--navy); margin: 18px 0 12px auto; width: 330px; }
  .tagline { font-size: 12px; letter-spacing: 0.5px; text-transform: uppercase; text-align: left; padding-left: 50px; }
</style>
</head>
<body>
  <section class="card card-front" aria-label="Card front">
    <div class="front-brand">
      <span class="brand-main">ARCVALE</span>
      <span class="brand-sub">WEALTH PARTNERS</span>
    </div>
  </section>

  <section class="card card-back" aria-label="Card back">
    <div class="back-band">
      <div class="back-brand">
        <span class="brand-main">ARCVALE</span>
        <span class="brand-sub">WEALTH PARTNERS</span>
      </div>
    </div>
    <div class="contact">
      <p class="contact-name">Miriam Okafor</p>
      <p class="contact-title">Managing Director</p>
      <div class="rule-short"></div>
      <p class="contact-address">Your address, City<br>State, Zip 0000</p>
      <ul class="contact-lines">
        <li>000 000 000
          <svg viewBox="0 0 24 24" aria-hidden="true"><path d="M6.6 10.8a15.5 15.5 0 0 0 6.6 6.6l2.2-2.2a1 1 0 0 1 1-.25 11.4 11.4 0 0 0 3.6.57 1 1 0 0 1 1 1V20a1 1 0 0 1-1 1A17 17 0 0 1 3 4a1 1 0 0 1 1-1h3.5a1 1 0 0 1 1 1c0 1.25.2 2.45.57 3.57a1 1 0 0 1-.25 1z"/></svg>
        </li>
        <li>hello@arcvale.example
          <svg viewBox="0 0 24 24" aria-hidden="true"><path d="M2 5h20v14H2z M4 7v.5l8 5 8-5V7l-8 5z" fill-rule="evenodd"/></svg>
        </li>
        <li>arcvale.example
          <svg viewBox="0 0 24 24" aria-hidden="true"><path d="M12 2a10 10 0 1 0 0 20 10 10 0 0 0 0-20zm6.9 9h-3a15 15 0 0 0-1.3-5.6A8 8 0 0 1 18.9 11zM12 4c.9 1.2 1.8 3.6 1.9 7h-3.8C10.2 7.6 11.1 5.2 12 4zM9.4 5.4A15 15 0 0 0 8.1 11h-3a8 8 0 0 1 4.3-5.6zM5.1 13h3a15 15 0 0 0 1.3 5.6A8 8 0 0 1 5.1 13zM12 20c-.9-1.2-1.8-3.6-1.9-7h3.8c-.1 3.4-1 5.8-1.9 7zm2.6-1.4a15 15 0 0 0 1.3-5.6h3a8 8 0 0 1-4.3 5.6z"/></svg>
        </li>
      </ul>
      <div class="rule-long"></div>
      <p class="tagline">The Path From Saver to Steward</p>
    </div>
  </section>
</body>
</html>
```